Larkfield Ridge Management

I need a professional website. My current website is larkfieldridgemanagement.com and I hate it. It was created with some AI tool very quickly because I needed a site up and running with no advanced notice. I’m open to all designs .. I trust you, the professionals will deliver the results I’m anxiously awaiting! :)

```html
<!DOCTYPE html>
<html lang="en">
<head>
<meta charset="utf-8">
<title>Larkfield Ridge Management</title>
<link href="https://fonts.googleapis.com/css2?family=Montserrat:wght@400;500;600;700&family=Rubik:wght@800&display=swap" rel="stylesheet">
<style>
:root{
  --navy:#22335a;
  --navy-deep:#1c2a4c;
  --red:#d22a2f;
  --ink:#1f1f1f;
  --muted:#555a63;
  --white:#ffffff;
  --footer-dark:#2b2f37;
}
*{box-sizing:border-box;margin:0;padding:0}
html,body{width:1200px;height:3240px;overflow:hidden}
body{position:relative;background:var(--white);font-family:'Montserrat',sans-serif;color:var(--ink)}
.abs{position:absolute}
h1,h2,h3{font-weight:400}

/* header */
.site-header{position:absolute;left:0;top:0;width:1200px;height:82px;background:var(--white);z-index:5}
.brand{position:absolute;left:110px;top:0;height:82px;display:flex;align-items:center;gap:10px;font-weight:700;font-size:15px;line-height:19px;color:var(--navy)}
.brand-square{width:18px;height:18px;background:var(--red);flex:none}
.main-nav{position:absolute;left:374px;top:36px;display:flex;gap:42px;font-size:16px;font-weight:500;color:#333}
.main-nav .active{font-weight:700;color:var(--navy);position:relative}
.main-nav .active::after{content:"";position:absolute;left:0;right:0;top:38px;height:4px;background:var(--navy)}
.header-phone{position:absolute;left:748px;top:25px;display:flex;align-items:center;gap:8px;font-size:19px;font-weight:500;color:var(--navy)}
.phone-badge{width:34px;height:34px;border-radius:50%;background:var(--navy);display:flex;align-items:center;justify-content:center}
.btn-arrow{position:absolute;background:var(--red);color:var(--white);font-weight:700;display:flex;align-items:center;justify-content:center;clip-path:polygon(0 0,calc(100% - 16px) 0,100% 50%,calc(100% - 16px) 100%,0 100%)}

/* hero */
.hero-band{left:0;top:82px;width:1200px;height:780px;background:var(--red);clip-path:polygon(0 0,100% 0,100% 607px,50% 780px,0 607px)}
.hero-photo{left:0;top:82px;width:1200px;height:780px;background:linear-gradient(180deg,#4f9ae4 0%,#8ec1ec 30%,#9a8f86 55%,#6d7a5a 78%,#5d6260 100%);clip-path:polygon(0 0,100% 0,100% 578px,50% 761px,0 578px)}
.hero-title{left:112px;top:200px;font-family:'Rubik',sans-serif;font-weight:800;font-size:58px;line-height:72px;color:var(--white)}
.hero-sub{left:112px;top:350px;font-size:27px;color:var(--white)}

/* section heads */
.sec-head{left:0;width:1200px;text-align:center;font-size:44px;line-height:54px;font-weight:400;color:var(--ink)}
.sec-head b{color:var(--navy);font-weight:700}
.red-bar{height:5px;background:var(--red)}
.sec-text{left:0;width:1200px;text-align:center;font-size:15.5px;line-height:27px;color:var(--muted)}

/* cards */
.card{position:absolute;top:1248px;width:316px;height:435px;filter:drop-shadow(0 3px 6px rgba(0,0,0,.18))}
.card-shape{position:absolute;inset:0;background:var(--white);clip-path:polygon(50% 0,100% 48px,100% 100%,0 100%,0 48px)}
.card-img{position:absolute;left:9px;top:9px;width:298px;height:371px;clip-path:polygon(50% 0,100% 44px,100% 100%,0 100%,0 44px)}
.card-label{position:absolute;left:0;width:316px;top:394px;text-align:center;font-size:22px;font-weight:500}
.card-mid .card-img{height:230px}
.card-icon{position:absolute;left:133px;top:210px;width:50px;height:50px;border-radius:50%;background:var(--red);border:3px solid var(--white);display:flex;align-items:center;justify-content:center}
.card-title{position:absolute;left:0;width:316px;top:272px;text-align:center;font-size:21px;font-weight:700;color:var(--navy)}
.card-desc{position:absolute;left:20px;width:276px;top:306px;text-align:center;font-size:11.5px;line-height:20.5px;color:#333}
.card-arrow{position:absolute;left:143px;top:394px}
.slider-arrow{position:absolute;top:1462px;width:30px;height:30px;border-radius:50%;border:2px solid;display:flex;align-items:center;justify-content:center}

/* about */
.about{left:0;top:1788px;width:1200px;height:558px;background:var(--navy)}
.about-title{left:112px;top:1848px;font-size:44px;font-weight:400;color:var(--white)}
.about-title b{font-weight:700}
.about-text{left:111px;top:1938px;width:425px;font-size:15px;line-height:29px;color:var(--white);text-align:justify}
.about-text p+p{margin-top:5px}

/* footer */
.footer-red{left:0;top:2768px;width:1200px;height:472px;background:var(--red);clip-path:polygon(50% 0,100% 201px,100% 100%,0 100%,0 201px)}
.footer-photo{left:0;top:2768px;width:1200px;height:472px;background:linear-gradient(180deg,#3a3f48 0%,#2b2f37 55%,#23272d 100%);clip-path:polygon(50% 22px,100% 226px,100% 100%,0 100%,0 226px)}
.foot-h{font-size:22px;font-weight:700;color:var(--white)}
.foot-links{left:116px;top:3030px;list-style:none;font-size:14px;line-height:27.5px;color:var(--white)}
.foot-brand{left:450px;top:3018px;width:300px;text-align:center;font-size:22px;line-height:28px;font-weight:700;color:var(--white)}
.contact-row{position:absolute;left:822px;display:flex;align-items:center;gap:16px;font-size:13.5px;color:var(--white)}
.contact-icon{width:24px;height:24px;border-radius:50%;background:var(--white);display:flex;align-items:center;justify-content:center}
.foot-rule{left:112px;top:3197px;width:978px;height:1px;background:rgba(255,255,255,.5)}
.copyright{left:0;top:3214px;width:1200px;text-align:center;font-size:12px;color:var(--white)}
</style>
</head>
<body>

<header class="site-header">
  <div class="brand"><span class="brand-square"></span><span>Larkfield Ridge<br>Management</span></div>
  <nav class="main-nav">
    <span class="active">Home</span><span>Services</span><span>About</span>
  </nav>
  <div class="header-phone">
    <span class="phone-badge"><svg width="18" height="18" viewBox="0 0 24 24"><path fill="#fff" d="M6.6 10.8a15 15 0 0 0 6.6 6.6l2.2-2.2a1 1 0 0 1 1-.25 11.4 11.4 0 0 0 3.6.57 1 1 0 0 1 1 1V20a1 1 0 0 1-1 1A17 17 0 0 1 3 4a1 1 0 0 1 1-1h3.5a1 1 0 0 1 1 1c0 1.25.2 2.45.57 3.57a1 1 0 0 1-.25 1z"/></svg></span>
    +1 555 014 2736
  </div>
  <a class="btn-arrow" style="left:962px;top:19px;width:122px;height:42px;font-size:17px;padding-right:12px">Contact</a>
</header>

<section class="hero">
  <div class="abs hero-band"></div>
  <div class="abs hero-photo" role="img" aria-label="Row of suburban two-storey houses along a tree-lined street under a blue sky"></div>
  <h1 class="abs hero-title">Property Management That<br>Protects Your Investment</h1>
  <p class="abs hero-sub">A true partner, not just a vendor</p>
  <a class="btn-arrow" style="left:112px;top:414px;width:236px;height:43px;font-size:17.5px;padding-right:14px">Schedule Consultation</a>
</section>

<section class="solutions">
  <h2 class="abs sec-head" style="top:949px">Strategic Property<br><b>Management Solutions</b></h2>
  <div class="abs red-bar" style="left:559px;top:1070px;width:82px"></div>
  <p class="abs sec-text" style="top:1107px">Our analysis demonstrates that effective property oversight originates from meticulous<br>operational planning, transparent communication channels, and data-driven<br>performance metrics across every asset class.</p>

  <div class="slider-arrow" style="left:39px;border-color:var(--red)"><svg width="14" height="14" viewBox="0 0 14 14"><path d="M9 2 4 7l5 5" fill="none" stroke="#d22a2f" stroke-width="2"/></svg></div>
  <div class="slider-arrow" style="left:1124px;border-color:#aaa"><svg width="14" height="14" viewBox="0 0 14 14"><path d="m5 2 5 5-5 5" fill="none" stroke="#999" stroke-width="2"/></svg></div>

  <article class="card" style="left:109px">
    <div class="card-shape"></div>
    <div class="card-img" role="img" aria-label="Hand pointing at a fanned paint colour swatch book" style="background:linear-gradient(160deg,#e8e2d6,#d9c9a4 50%,#6fa7a7)"></div>
    <div class="card-label">Basic Service</div>
  </article>

  <article class="card card-mid" style="left:441px">
    <div class="card-shape"></div>
    <div class="card-img" role="img" aria-label="Bright living room with arched walls, sofa and pendant lights" style="background:linear-gradient(180deg,#efe7df,#d9c3a8 60%,#c9b7a3)"></div>
    <div class="card-icon"><svg width="26" height="26" viewBox="0 0 24 24"><circle cx="12" cy="12" r="4" fill="none" stroke="#fff" stroke-width="2.2"/><path d="M12 2v4M12 18v4M2 12h4M18 12h4M4.9 4.9l2.8 2.8M16.3 16.3l2.8 2.8M4.9 19.1l2.8-2.8M16.3 7.7l2.8-2.8" stroke="#fff" stroke-width="2.2"/></svg></div>
    <h3 class="card-title">Intermediate Service</h3>
    <p class="card-desc">Describe important details like price, value, length of service, and why it's unique. Or use these sections to showcase different key values of your products or services.</p>
    <svg class="card-arrow" width="30" height="20" viewBox="0 0 30 20"><path d="M1 10h26M19 2l8 8-8 8" fill="none" stroke="#d22a2f" stroke-width="2.4"/></svg>
  </article>

  <article class="card" style="left:771px">
    <div class="card-shape"></div>
    <div class="card-img" role="img" aria-label="Desk with a vase of calla lilies, a small lamp and a hand writing in a notebook" style="background:linear-gradient(180deg,#8d7b68,#b8a38c 55%,#e6e3df)"></div>
    <div class="card-label">Advanced Service</div>
  </article>
</section>

<section class="about-section">
  <div class="abs about"></div>
  <svg class="abs" style="left:0;top:1788px" width="1200" height="558" viewBox="0 0 1200 558">
    <polygon points="700,0 728,0 596,279 692,558 664,558 586,279" fill="#d22a2f"/>
  </svg>
  <div class="abs" role="img" aria-label="Modern bedroom with built-in shelves, a desk with a chair and a bed with yellow cushions"
       style="left:0;top:1788px;width:1200px;height:558px;background:linear-gradient(120deg,#5f7478,#a9bfc3 45%,#cfd8da 70%,#8fb3c2);clip-path:polygon(727px 0,100% 0,100% 100%,689px 100%,602px 279px)"></div>
  <h2 class="abs about-title">About <b>Us</b></h2>
  <div class="abs red-bar" style="left:113px;top:1910px;width:82px"></div>
  <div class="abs about-text">
    <p>Our organization delivers comprehensive property management solutions that optimize asset performance and tenant satisfaction. By integrating advanced analytics with proven operational frameworks, our specialists ensure each property achieves sustained value appreciation.</p>
    <p>Drawing on decades of collective expertise, the team facilitates regulatory compliance, cost efficiency, and proactive maintenance.</p>
  </div>
  <a class="btn-arrow" style="left:111px;top:2239px;width:148px;height:41px;font-size:17px;padding-right:12px">Read More</a>
</section>

<section class="cta">
  <h2 class="abs sec-head" style="top:2424px;font-size:45px">Ready to <b>Protect Your Investment?</b></h2>
  <div class="abs red-bar" style="left:561px;top:2492px;width:82px"></div>
  <p class="abs sec-text" style="top:2538px;font-size:14.5px">Please complete the inquiry form to facilitate an initial consultation, enabling our<br>team to demonstrate how comprehensive property management solutions can<br>enhance operational efficiency and stakeholder satisfaction.</p>
  <a class="btn-arrow" style="left:552px;top:2659px;width:124px;height:43px;font-size:17px;padding-right:12px">Contact</a>
</section>

<footer>
  <div class="abs footer-red"></div>
  <div class="abs footer-photo" role="img" aria-label="Darkened view of suburban houses along a street"></div>
  <h3 class="abs foot-h" style="left:116px;top:2990px">Quick Links</h3>
  <ul class="abs foot-links"><li>Home</li><li>About Us</li><li>Services</li><li>Contact</li></ul>
  <div class="abs foot-brand">Larkfield Ridge<br>Management</div>
  <h3 class="abs foot-h" style="left:823px;top:2984px">Contact Info</h3>
  <div class="contact-row" style="top:3029px"><span class="contact-icon"><svg width="12" height="14" viewBox="0 0 12 16"><path d="M6 0a6 6 0 0 0-6 6c0 4.5 6 10 6 10s6-5.5 6-10a6 6 0 0 0-6-6zm0 8.5A2.5 2.5 0 1 1 6 3.5a2.5 2.5 0 0 1 0 5z" fill="#2b2f37"/></svg></span>Lorem Ipsum,USA -437916</div>
  <div class="contact-row" style="top:3071px"><span class="contact-icon"><svg width="13" height="13" viewBox="0 0 24 24"><path fill="#2b2f37" d="M6.6 10.8a15 15 0 0 0 6.6 6.6l2.2-2.2a1 1 0 0 1 1-.25 11.4 11.4 0 0 0 3.6.57 1 1 0 0 1 1 1V20a1 1 0 0 1-1 1A17 17 0 0 1 3 4a1 1 0 0 1 1-1h3.5a1 1 0 0 1 1 1c0 1.25.2 2.45.57 3.57a1 1 0 0 1-.25 1z"/></svg></span>+1 555 014 2736</div>
  <div class="contact-row" style="top:3114px"><span class="contact-icon"><svg width="13" height="10" viewBox="0 0 16 12"><rect x="0.5" y="0.5" width="15" height="11" fill="none" stroke="#2b2f37"/><path d="M1 1l7 6 7-6" fill="none" stroke="#2b2f37"/></svg></span>info@larkfieldridgemanagement.com</div>
  <div class="abs foot-rule"></div>
  <p class="abs copyright">© 2026 Larkfield Ridge Management . All Rights Reserved.</p>
</footer>

</body>
</html>
```